Business Cards Design for the electrical wholesaler: clean bold dynamic :)

We need a business card design that would follow our latest brand guidelines. As an electrical wholesaler we want to bring a fresh look and feel into the industry. The design should be clean bold and dynamic. It should come alive with the renewed energy of our green colour. Our grey colour should keep things balanced and complement the notion of maturity and responsibility. We employ Lato as a corporate font however are not bound by this font and we’re open to interpretation here.

Target Market(s)

Electrical contractors

Industry/Entity Type

Business

Contact Information for Business Card

Logo
Name & Surname: Halyna Dorosh
Job Title: Director of Marketing
Email: halya.dorosh@quillmail.example
Cell phone: 780.555.0239
Address: 20517 - 87 Ave. Edmonton, AB, Canada. T6K 4N8
Business Phone: 780.555.0184
Website: www.brovix.example

Font styles to use
Other font styles liked:
• Lato

Requirements
Must have
• Logo & website
Nice to have
• Brand elements - some of them you may find in the attached Brand Guidelines (e.g. three lines on the background signifying "W")

```html
<!DOCTYPE html>
<html lang="en">
<head>
<meta charset="utf-8">
<title>Brovix Business Card</title>
<link rel="stylesheet" href="https://fonts.googleapis.com/css2?family=Roboto:wght@400;500&display=swap">
<style>
  :root {
    --page: #b9b9b9;
    --green: #7ab929;
    --green-deep: #5da532;
    --green-text: #77b82a;
    --charcoal: #45494d;
    --ink: #3c3f42;
    --paper: #f4f4f3;
    --soft-text: #e2e3e3;
  }
  * { box-sizing: border-box; margin: 0; padding: 0; }
  html, body { width: 1200px; height: 576px; overflow: hidden; }
  body {
    background: var(--page);
    font-family: "Roboto", Arial, sans-serif;
    position: relative;
  }
  .card {
    position: absolute;
    top: 138px;
    width: 484px;
    height: 292px;
    border-radius: 14px;
    overflow: hidden;
  }
  .card--front {
    left: 82px;
    background: linear-gradient(135deg, var(--green) 0%, var(--green-deep) 100%);
  }
  .card--back {
    left: 600px;
    background: var(--charcoal);
  }
  .wordmark {
    position: absolute;
    display: flex;
    align-items: center;
    gap: 10px;
    font-weight: 500;
    color: var(--charcoal);
    letter-spacing: -0.5px;
    line-height: 1;
  }
  .wordmark__dot { border-radius: 50%; flex: none; }
  .card--front .wordmark {
    left: 50%;
    top: 146px;
    transform: translate(-50%, -50%);
    font-size: 52px;
  }
  .card--front .wordmark__dot { width: 30px; height: 30px; background: #ffffff; }

  .back__top {
    position: absolute;
    inset: 0 0 auto 0;
    height: 149px;
    background: var(--paper);
  }
  .back__stripe {
    position: absolute;
    left: 0; right: 0;
    top: 149px;
    height: 6px;
    background: var(--green);
  }
  .back__tab {
    position: absolute;
    left: -34px;
    top: 50px;
    width: 46px;
    height: 46px;
    border-radius: 50%;
    background: var(--green);
  }
  .person {
    position: absolute;
    left: 29px;
    top: 56px;
  }
  .person__name {
    font-size: 21px;
    font-weight: 500;
    color: var(--green-text);
    line-height: 1.1;
  }
  .person__title {
    font-size: 12.5px;
    color: var(--ink);
    margin-top: 5px;
  }
  .card--back .wordmark {
    right: 22px;
    top: 58px;
    font-size: 38px;
  }
  .card--back .wordmark__dot { width: 24px; height: 24px; background: var(--green); }

  .contact {
    position: absolute;
    left: 28px;
    top: 188px;
    color: var(--soft-text);
    font-size: 12.5px;
    line-height: 1.45;
  }
  .contact__address { font-style: normal; }
  .contact__lines { display: flex; flex-direction: column; gap: 2px; margin-top: 6px; }
  .contact__row { display: flex; align-items: center; gap: 10px; }
  .contact__item { display: flex; align-items: center; gap: 6px; white-space: nowrap; }
  .icon { width: 13px; height: 13px; flex: none; }
</style>
</head>
<body>

<section class="card card--front" aria-label="Business card front">
  <div class="wordmark"><span class="wordmark__dot"></span>brovix</div>
</section>

<section class="card card--back" aria-label="Business card back">
  <div class="back__top"></div>
  <div class="back__stripe"></div>
  <div class="back__tab"></div>

  <div class="person">
    <p class="person__name">Halyna Dorosh</p>
    <p class="person__title">Director of Marketing</p>
  </div>

  <div class="wordmark"><span class="wordmark__dot"></span>brovix</div>

  <div class="contact">
    <address class="contact__address">
      20517 - 87 Ave. Edmonton,<br>AB, Canada. T6K 4N8
    </address>
    <div class="contact__lines">
      <div class="contact__row">
        <span class="contact__item">
          <svg class="icon" viewBox="0 0 14 14" aria-hidden="true">
            <circle cx="7" cy="7" r="6.3" fill="none" stroke="#e2e3e3" stroke-width="1"/>
            <path d="M4 5.2 Q7 3.4 10 5.2 L9.4 6.3 L8.3 6 L8.3 5.3 Q7 4.9 5.7 5.3 L5.7 6 L4.6 6.3 Z M4.8 7 H9.2 L9.6 10 H4.4 Z" fill="#e2e3e3"/>
          </svg>780.555.0184
        </span>
        <span class="contact__item">
          <svg class="icon" viewBox="0 0 14 14" aria-hidden="true">
            <circle cx="7" cy="7" r="6.3" fill="none" stroke="#e2e3e3" stroke-width="1"/>
            <rect x="5" y="3.4" width="4" height="7.2" rx="0.8" fill="#e2e3e3"/>
            <rect x="5.7" y="4.3" width="2.6" height="4.4" fill="#45494d"/>
          </svg>780.555.0239
        </span>
      </div>
      <div class="contact__row">
        <span class="contact__item">
          <svg class="icon" viewBox="0 0 14 14" aria-hidden="true">
            <circle cx="7" cy="7" r="6.3" fill="none" stroke="#e2e3e3" stroke-width="1"/>
            <rect x="3.8" y="4.8" width="6.4" height="4.4" fill="#e2e3e3"/>
            <path d="M3.8 4.8 L7 7.3 L10.2 4.8" fill="none" stroke="#45494d" stroke-width="0.8"/>
          </svg>halya.dorosh@quillmail.example
        </span>
        <span class="contact__item">
          <svg class="icon" viewBox="0 0 14 14" aria-hidden="true">
            <circle cx="7" cy="7" r="6.3" fill="none" stroke="#e2e3e3" stroke-width="1"/>
            <circle cx="7" cy="7" r="3.6" fill="none" stroke="#e2e3e3" stroke-width="0.9"/>
            <ellipse cx="7" cy="7" rx="1.5" ry="3.6" fill="none" stroke="#e2e3e3" stroke-width="0.8"/>
            <path d="M3.4 7 H10.6" stroke="#e2e3e3" stroke-width="0.8"/>
          </svg>www.brovix.example
        </span>
      </div>
    </div>
  </div>
</section>

</body>
</html>
```